Brevard Trade Partners - we are Asian sourcing agents

We are sourcing agents based in the USA and we act as sourcing agents for clients in throughout the world. We focus primarily on custom sewn goods. So basically companies who do not have the in-house expertise to do it themselves, come to us and have us find suitable factories in Asia to do the production. We are middlemen. We find the factories...quote the project...manage the quality control and then deliver the goods directly to our customer's door. We pride ourselves in making the communication very easy and precise.

Current page is www.brevardtradepartners.com

I am not happy w/ the overall look. The spacing...the photos, the fonts...the design elements...the pictures. I want a cool, crisp design that conveys professionalism and clearly depicts/explains what we do.

Requirements
Must have
• use my logo....I like it...it was designed by someone on this website.
Nice to have
• a video/animation of the entire process would be wonderful. Showing initial contact with our office in the USA...then to my correspondence with my offices in Taiwan and in Hong Kong...and then back and fort w/ the customer.....and then between my people in Hong Kong/Taiwan with the local factories......and then a quote is generated and sent to my client......to samples being made and sent for approval.....to a PO being generated......to final samples being sent.....to the order being shipped and delivered to the clients warehouse. I was thinking of an animation showing arrows and text showing the back and forth communication and explaining how the process flows.

```html
<!DOCTYPE html>
<html lang="en">
<head>
<meta charset="utf-8">
<title>Brevard Trade Partners — Asian Sourcing Agents</title>
<link rel="stylesheet" href="https://fonts.googleapis.com/css2?family=Open+Sans:ital,wght@0,300;0,400;0,600;0,700;1,300&display=swap">
<style>
:root{
  --page:#ebebeb;
  --white:#ffffff;
  --navy:#0c1547;
  --green:#66961e;
  --green-dark:#4f7a12;
  --ink:#1a1a1a;
  --muted:#555555;
  --rule:#dddddd;
}
*{margin:0;padding:0;box-sizing:border-box}
html,body{width:1200px;height:2287px;overflow:hidden;background:var(--page);font-family:Arial,Helvetica,sans-serif;color:var(--ink)}
.site{position:absolute;left:99px;top:35px;width:1002px;height:2138px;background:var(--white)}
.abs{position:absolute}

/* header */
.brand{left:35px;top:32px;font-family:'Open Sans',sans-serif;font-weight:700;font-size:26px;color:var(--navy);display:flex;align-items:center;gap:10px;letter-spacing:.2px}
.brand-mark{width:14px;height:14px;background:var(--green)}
.nav{right:42px;top:38px;display:flex;gap:38px;align-items:center;font-family:'Open Sans',sans-serif;font-size:13px;font-weight:600;color:var(--ink)}
.nav a{color:inherit;text-decoration:none}
.nav .active{background:var(--green);color:var(--white);padding:7px 14px;border-radius:2px}

/* hero */
.hero{left:0;top:102px;width:1002px;height:468px;background:linear-gradient(100deg,#3a302a 0%,#6b4a34 40%,#a6764f 65%,#d49b67 100%)}
.hero-title{right:46px;top:195px;text-align:right;font-family:'Open Sans',sans-serif;font-weight:300;color:var(--white)}
.hero-title h1{font-weight:300;font-size:37px;line-height:1.2}
.hero-title p{font-size:22px;line-height:1.3}
.slide-btn{width:42px;height:42px;border-radius:50%;background:var(--white);top:415px}

/* intro */
.intro-title{left:0;width:1002px;top:603px;text-align:center;font-family:'Open Sans',sans-serif;font-weight:700;font-size:26px;color:var(--navy)}
.intro-title span{color:var(--green)}
.intro-rule{left:425px;top:645px;width:152px;height:1px;background:var(--rule)}
.intro-text{left:50px;width:902px;top:661px;text-align:center;font-size:12px;line-height:20px;color:var(--muted)}

/* product grid */
.tile{width:212px;height:137px;border:1px solid #e3e3e3;box-shadow:0 12px 10px -8px rgba(0,0,0,.25);padding:4px;background:var(--white)}
.tile .photo{width:100%;height:100%}
.tile-label{font-family:'Open Sans',sans-serif;font-weight:700;font-size:14px;color:var(--ink)}
.view-more{width:214px;height:139px;background:var(--green);box-shadow:0 12px 10px -8px rgba(0,0,0,.3);color:var(--white);font-family:'Open Sans',sans-serif;font-weight:300;font-size:30px;line-height:30px;text-align:center;display:flex;align-items:center;justify-content:center}

/* navy band */
.process{left:0;top:1183px;width:1002px;height:397px;background:var(--navy);color:var(--white)}
.process h2{font-family:'Open Sans',sans-serif;font-weight:700;font-size:24px}
.process p{font-size:11px;line-height:20px}
.step-icon{width:34px;height:34px}
.video{left:546px;top:106px;width:419px;height:169px;background:linear-gradient(90deg,#283a5a,#8a97a8 50%,#b9b49a)}
.play{left:197px;top:62px}

/* call to action */
.cta{left:0;top:1580px;width:1002px;height:201px;background:linear-gradient(180deg,#a9b9c4 0%,#8a9a8c 45%,#d4d6d6 75%,#eeeeee 100%)}
.cta-text{left:35px;top:77px;font-family:'Open Sans',sans-serif;font-style:italic;font-weight:300;font-size:26px;line-height:32px;color:var(--ink)}
.cta-btn{left:660px;top:79px;width:238px;height:49px;background:var(--green);border-radius:3px;color:var(--white);font-family:'Open Sans',sans-serif;font-weight:700;font-size:21px;display:flex;align-items:center;justify-content:center}

/* footer lists */
.links h3{font-family:'Open Sans',sans-serif;font-weight:700;font-size:15px;color:var(--ink);margin-bottom:14px}
.links ul{list-style:none}
.links li{font-size:11px;line-height:24px;color:var(--muted);padding-left:20px;position:relative}
.links li::before{content:"";position:absolute;left:2px;top:9px;border-left:5px solid #555;border-top:3px solid transparent;border-bottom:3px solid transparent}

/* bottom bar */
.legal{font-size:11px;line-height:18px;color:var(--muted)}
.legal b{color:var(--ink);font-weight:400}
.phone{font-size:15px;color:var(--ink)}
.social{left:877px;top:2214px;display:flex;gap:9px}
.social span{width:34px;height:34px;border-radius:50%;background:var(--navy)}
</style>
</head>
<body>
<main class="site">
  <header>
    <div class="abs brand"><span class="brand-mark"></span>Brevard Trade Partners</div>
    <nav class="abs nav">
      <a class="active" href="#">HOME</a><a href="#">PRODUCT</a><a href="#">CATEGORIES</a><a href="#">ABOUT US</a><a href="#">REQUEST QUOTE</a>
    </nav>
  </header>

  <section class="abs hero" role="img" aria-label="Close-up of hands guiding fabric under a sewing machine needle">
    <div class="abs hero-title">
      <h1>Asian Outsourcing Made Easy!</h1>
      <p>Custom Sewn Goods Made to Your Specifications</p>
    </div>
    <svg class="abs slide-btn" style="left:857px" viewBox="0 0 42 42"><path d="M24 14l-7 7 7 7" fill="none" stroke="#222" stroke-width="2"/></svg>
    <svg class="abs slide-btn" style="left:906px" viewBox="0 0 42 42"><path d="M18 14l7 7-7 7" fill="none" stroke="#222" stroke-width="2"/></svg>
  </section>

  <h2 class="abs intro-title">SOURCING CUSTOM GOODS <span>IN CHINA</span></h2>
  <div class="abs intro-rule"></div>
  <p class="abs intro-text">We outsource sewing services direct from China. Our long-established and extensive network of offshore factory-partners provides our clients with access to a wide variety of contract sewing expertise from Chinese manufacturers. Clients only need to communicate with our US agents, but will have the benefits of the cost savings<br>&amp; quality workmanship from offshore outsourcing from Asia.</p>

  <div class="abs tile" style="left:35px;top:766px"><div class="photo" role="img" aria-label="Fabric being sewn on a machine" style="background:linear-gradient(135deg,#6c5a55,#c23a2e)"></div></div>
  <div class="abs tile-label" style="left:35px;top:920px">SEWN GOODS</div>
  <div class="abs tile" style="left:275px;top:766px"><div class="photo" role="img" aria-label="Black messenger bag with red stripe" style="background:linear-gradient(135deg,#fff,#3a3a3a 45%,#b52a2a 60%,#fff)"></div></div>
  <div class="abs tile-label" style="left:275px;top:920px">BAGS</div>
  <div class="abs tile" style="left:514px;top:766px"><div class="photo" role="img" aria-label="Pair of work gloves" style="background:linear-gradient(135deg,#fff,#2b2b2b 40%,#cfcfcf 65%,#fff)"></div></div>
  <div class="abs tile-label" style="left:514px;top:920px">GLOVES</div>
  <div class="abs tile" style="left:753px;top:766px"><div class="photo" role="img" aria-label="Motorcycle under a fitted cover" style="background:linear-gradient(135deg,#fff,#1e2a6e 45%,#aaa 75%,#fff)"></div></div>
  <div class="abs tile-label" style="left:753px;top:920px">COVERS</div>

  <div class="abs tile" style="left:35px;top:964px"><div class="photo" role="img" aria-label="Row of colourful phone cases" style="background:linear-gradient(90deg,#2a3aa8,#7a2aa8,#c22a7a,#d43a2a,#d48a2a)"></div></div>
  <div class="abs tile-label" style="left:35px;top:1120px">CASES</div>
  <div class="abs tile" style="left:275px;top:964px"><div class="photo" role="img" aria-label="White medical pad" style="background:linear-gradient(160deg,#fff,#dfe3ee 50%,#7a9ad4 80%,#fff)"></div></div>
  <div class="abs tile-label" style="left:275px;top:1120px">MEDICAL</div>
  <div class="abs tile" style="left:514px;top:964px"><div class="photo" role="img" aria-label="Group of golf bags" style="background:linear-gradient(135deg,#fff,#2a2a2a 35%,#c22a2a 60%,#fff)"></div></div>
  <div class="abs tile-label" style="left:514px;top:1120px">SPORTING GOODS</div>
  <div class="abs view-more" style="left:753px;top:964px">VIEW<br>MORE</div>

  <section class="abs process">
    <h2 class="abs" style="left:35px;top:42px">DON’T GO AT IT ALONE!</h2>
    <p class="abs" style="left:35px;top:102px;width:470px">Brevard Trade Partners has been sourcing custom sewn goods in Asia since 1998. We work with our clients by matching their unique production needs with the best possible China sewing factories. We manage the entire process from start to finish, by first identifying the best factories to quote each job.</p>
    <svg class="abs step-icon" style="left:35px;top:197px" viewBox="0 0 34 34"><path d="M8 28V16a8 8 0 0 1 8-8h6" fill="none" stroke="#66961e" stroke-width="6"/><path d="M20 1l12 7-12 8z" fill="#66961e"/></svg>
    <p class="abs" style="left:83px;top:190px;width:422px">The next step is negotiating the best (fair) price possible. We complete the process by monitoring the quality of the goods during production, and then managing the ocean logistics, customs clearances and local delivery right to your door.</p>
    <svg class="abs step-icon" style="left:35px;top:272px" viewBox="0 0 34 34"><circle cx="17" cy="17" r="10" fill="none" stroke="#66961e" stroke-width="6" stroke-dasharray="5 3"/><circle cx="17" cy="17" r="8" fill="#66961e"/><circle cx="17" cy="17" r="3.5" fill="#0c1547"/></svg>
    <p class="abs" style="left:83px;top:266px;width:422px">Our services and our total commitment to customer satisfaction help level the playing field by giving our customers access to low cost, high quality China contract sewing.</p>

    <h2 class="abs" style="left:544px;top:42px">HOW IT WORKS</h2>
    <div class="abs video" role="img" aria-label="Video still of a worker at a sewing factory">
      <svg class="abs play" width="46" height="46" viewBox="0 0 46 46"><circle cx="23" cy="23" r="21" fill="#222" fill-opacity=".75" stroke="#fff" stroke-width="3"/><path d="M18 13l15 10-15 10z" fill="#fff"/></svg>
    </div>
    <p class="abs" style="left:544px;top:292px;width:420px">Watch how a project moves from first call to factory, samples, order and delivery to your warehouse.</p>
  </section>

  <section class="abs cta" role="img" aria-label="Bright terrace overlooking a lake">
    <p class="abs cta-text">Please contact us for immediate consultation<br>regarding your outsourcing project.</p>
    <div class="abs cta-btn">REQUEST A QUOTE</div>
  </section>

  <div class="abs links" style="left:35px;top:1812px">
    <h3>CUSTOM BAGS</h3>
    <ul><li>Athletic Bags</li><li>Backpacks</li><li>Computer Bags</li><li>Cooler Bags</li><li>Cosmetic Bags</li><li>Handbags</li><li>Messenger Bags</li><li>Shopping Bags</li><li>Tool Bags</li><li>Travel Bags</li><li>Yoga Bags</li></ul>
  </div>
  <div class="abs links" style="left:232px;top:1812px">
    <h3>CUSTOM BAGS</h3>
    <ul><li>ATV Covers</li><li>Chair Covers</li><li>Equipment Covers</li><li>Golf Cart Covers</li><li>Motorcycle Covers</li><li>Outdoor Furniture Covers</li><li>Outdoor Grill Cover</li><li>Personal Watercraft Covers</li><li>Snowmobile Covers</li></ul>
  </div>
  <div class="abs links" style="left:490px;top:1812px">
    <h3>CUSTOM MEDICAL</h3>
    <ul><li>Medical Equipment Covers</li><li>Medical Pads</li><li>Medical Sheets &amp; Bedding Supplies</li><li>Oxygen Tank Cases and Bags</li></ul>
  </div>
  <div class="abs links" style="left:490px;top:1962px">
    <h3>CUSTOM SEWN GOODS</h3>
    <ul><li>Pet Collars, Leashes, &amp; Harnesses</li><li>Socks</li><li>Yoga Mats</li><li>Yoga Gear and Accessories</li></ul>
  </div>
  <div class="abs links" style="left:808px;top:1812px">
    <h3>CUSTOM CASES</h3>
    <ul><li>Cosmetic Cases</li><li>Phone Cases</li><li>Tool Bags and Tool Cases</li></ul>
  </div>
  <div class="abs links" style="left:808px;top:1962px">
    <h3>CUSTOM GLOVES</h3>
    <ul><li>Batting Gloves</li><li>Garden Gloves</li><li>Mechanic Gloves</li><li>Safety Gloves</li><li>Ski Gloves</li></ul>
  </div>
</main>

<footer>
  <p class="abs legal" style="left:134px;top:2201px">Brevard Trade Partners © 2015 • <b>Privacy Policy</b></p>
  <p class="abs legal" style="left:479px;top:2201px">Brevard Trade Partners, 48 Harbor Street<br>Suite 3, Dover, NH 03820</p>
  <p class="abs phone" style="left:479px;top:2242px">Phone : 603-555-0142</p>
  <div class="abs social" aria-label="Social links"><span></span><span></span><span></span><span></span><span></span></div>
</footer>
</body>
</html>
```